Residential Remodeling Contractor needs updated business card

I need a new design for my business card.
Name of the company is Ridgefell Construction. I need a card that commands presence, strength, integrity. I have been in business for 28 years. I am a Residential Remodeling Contractor that covers all aspects of a residential remodel and build.

```html
<!DOCTYPE html>
<html lang="en">
<head>
<meta charset="utf-8">
<title>Ridgefell Construction – Business Card</title>
<link rel="stylesheet" href="https://fonts.googleapis.com/css2?family=Montserrat:wght@400;500;600&display=swap">
<style>
  :root {
    --backdrop: #e8e6e9;
    --card-navy: #223d7c;
    --ink-white: #ffffff;
    --ink-soft: #e6eaf4;
  }
  * { margin: 0; padding: 0; box-sizing: border-box; }
  html, body {
    width: 1200px; height: 1108px; overflow: hidden;
    background: var(--backdrop);
    font-family: "Montserrat", sans-serif;
    color: var(--ink-white);
  }
  .canvas { position: relative; width: 1200px; height: 1108px; }
  .card {
    position: absolute;
    width: 740px; height: 443px;
    background: var(--card-navy);
  }
  .card--front { left: 241px; top: 68px; }
  .card--back { left: 248px; top: 589px; }

  .holder { position: absolute; left: 34px; top: 54px; }
  .holder__name { font-size: 27px; font-weight: 600; letter-spacing: 0.2px; line-height: 1.2; }
  .holder__role { font-size: 15px; font-weight: 400; color: var(--ink-soft); margin-top: 2px; margin-left: 2px; }

  .wordmark { text-transform: uppercase; font-weight: 500; color: var(--ink-white); line-height: 1.1; }
  .wordmark--small {
    position: absolute; right: 40px; top: 68px;
    font-size: 22px; letter-spacing: 1.5px; text-align: left;
  }
  .wordmark--small .wordmark__line2 { font-size: 17.5px; letter-spacing: 1.6px; margin-top: 4px; display: block; }

  .contacts { position: absolute; left: 30px; top: 326px; list-style: none; }
  .contacts li { display: flex; align-items: center; height: 31.5px; font-size: 15.5px; color: var(--ink-soft); }
  .contacts svg { width: 20px; height: 20px; margin-right: 12px; fill: var(--ink-white); flex: none; }

  .address {
    position: absolute; left: 528px; top: 372px;
    font-size: 16px; line-height: 20px; color: var(--ink-soft); font-style: normal;
  }

  .brand-lockup {
    position: absolute; left: 0; right: 0; top: 190px;
    display: flex; justify-content: center; align-items: center; gap: 26px;
  }
  .brand-lockup__mark { width: 22px; height: 22px; background: var(--ink-white); flex: none; }
  .wordmark--large { font-size: 46px; letter-spacing: 2px; }
  .wordmark--large .wordmark__line2 { display: block; font-size: 36px; letter-spacing: 2.4px; margin-top: 6px; }
</style>
</head>
<body>
<main class="canvas">
  <section class="card card--front" aria-label="Card front">
    <div class="holder">
      <p class="holder__name">Daniel Brooks</p>
      <p class="holder__role">Owner</p>
    </div>
    <p class="wordmark wordmark--small">Ridgefell<span class="wordmark__line2">Construction</span></p>
    <ul class="contacts">
      <li>
        <svg viewBox="0 0 24 24" aria-hidden="true"><path d="M2 9c0-3 4.5-5 10-5s10 2 10 5v1.5c0 .8-.7 1.5-1.5 1.5h-3c-.8 0-1.5-.7-1.5-1.5V9c-1.2-.5-2.5-.7-4-.7s-2.8.2-4 .7v1.5C8 11.3 7.3 12 6.5 12h-3C2.7 12 2 11.3 2 10.5z"/><path d="M6 13h12l2 8H4z"/><circle cx="12" cy="16.8" r="2.2" fill="#223d7c"/></svg>
        888.555.0142
      </li>
      <li>
        <svg viewBox="0 0 24 24" aria-hidden="true"><path d="M2 5h20v2l-10 6L2 7z"/><path d="M2 9.3l10 6 10-6V19H2z"/></svg>
        info@ridgefellconstruction.com
      </li>
      <li>
        <svg viewBox="0 0 24 24" aria-hidden="true"><circle cx="12" cy="12" r="10"/><path d="M7 6c2 0 3 1 3 2.5S8 10 8 12s2 2 2 4-1 3-2 3.5C5.5 18 4 15 4 12c0-2.5 1.2-4.7 3-6zM15 5c2 .8 3.5 2 4.5 4-1.5 0-2.5 1-2.5 2.5S19 14 19.7 15c-.8 1.8-2 3.2-3.7 4 .3-1.5 0-3-1.5-4s-1-3 .5-4-1.5-2.5 0-6z" fill="#223d7c"/></svg>
        www.ridgefellconstruction.com
      </li>
    </ul>
    <address class="address">245 Cedar Hollow Road<br>Brandon, MS 39042</address>
  </section>

  <section class="card card--back" aria-label="Card back">
    <div class="brand-lockup">
      <span class="brand-lockup__mark" aria-hidden="true"></span>
      <p class="wordmark wordmark--large">Ridgefell<span class="wordmark__line2">Construction</span></p>
    </div>
  </section>
</main>
</body>
</html>
```